Real Estate Company Looking for Business Card Designs for 3 Executives

Hello!
Thanks so much for considering our project! We are a real estate investment company located in Edmonton, Alberta called Bellhaven Group of Companies. We invest/develop both commercial and residential real estate and are looking to create 3 DOUBLE-SIDED business cards for 3 top executives in the company! (for some reason it won't let us select the double-sided option, but yes, the cards are double sided and would be happy to tip extra)

We have certain guidelines that we want our business cards to for sure follow - the back of the Business card has to be the Black Background Version of the Logo which has already been designed and linked as a file (first file). We want the entire back of the card to simply just be the black background logo. In terms of the front of the card, would like to see a smaller version of the white background logo (linked as the second file) in the top left hand corner - of course, feel free to get creative and we can make revisions together along the way! and Then after that, just text. We want the card to be sharp, clean, easy on the eyes and highly professional looking. We would like the card to include the Full name of the Company (Bellhaven Group of Companies), Name of the Person, Title, Phone, Email. If possible please provide the front part of the card for 3 people:

1) Bellhaven Group of Companies, Liora Quenby, Chief Financial Officer, 780-555-0142, lioraquenby@bellhavengroup.example

2) Bellhaven Group of Companies, Tobias Quenby, Chief Executive Officer, 780-555-0187, tobiasquenby@bellhavengroup.example

3) Bellhaven Group of Companies, Rui Delcourt, Chief Operations Officer, 587-555-0163, ruidelcourt@bellhavengroup.example

Thank you so much for considering our project & we look forward to seeing your designs!

```html
<!DOCTYPE html>
<html lang="en">
<head>
<meta charset="utf-8">
<title>Bellhaven Group of Companies — Business Card</title>
<link rel="stylesheet" href="https://fonts.googleapis.com/css2?family=Jost:wght@400&family=Tinos:wght@700&family=Arimo:wght@400&display=swap">
<style>
  :root {
    --backdrop: #d3d5d5;
    --paper: #f3f3f2;
    --ink: #141414;
    --ink-soft: #2b2b2b;
    --ghost: #dcdcdb;
    --card-black: #111111;
    --card-white-text: #f2f2f2;
  }
  * { margin: 0; padding: 0; box-sizing: border-box; }
  html, body {
    width: 1200px;
    height: 905px;
    overflow: hidden;
    background: var(--backdrop);
  }
  .canvas {
    width: 1200px;
    height: 905px;
    display: flex;
    align-items: center;
    justify-content: center;
    gap: 48px;
  }
  .card {
    position: relative;
    width: 525px;
    height: 300px;
    overflow: hidden;
  }
  .card--front { background: var(--paper); color: var(--ink); }
  .card--back {
    background: var(--card-black);
    display: flex;
    align-items: center;
    justify-content: center;
    padding: 0 40px;
  }

  .company-name {
    font-family: "Jost", sans-serif;
    font-weight: 400;
    text-transform: uppercase;
    letter-spacing: 0.28em;
    white-space: nowrap;
  }
  .card--front .company-name {
    position: absolute;
    top: 34px;
    left: 36px;
    font-size: 15px;
    color: var(--ink);
  }
  .card--back .company-name {
    font-size: 17px;
    color: var(--card-white-text);
    margin-right: -0.28em;
  }

  .person {
    position: absolute;
    top: 86px;
    left: 36px;
  }
  .person__name {
    font-family: "Tinos", serif;
    font-weight: 700;
    font-size: 26px;
    line-height: 1.1;
  }
  .person__title {
    font-family: "Arimo", sans-serif;
    font-size: 16px;
    color: var(--ink-soft);
    margin-top: 4px;
  }
  .person__rule {
    width: 12px;
    height: 2px;
    background: var(--ink);
    margin: 10px 0 12px;
  }
  .contact-list { list-style: none; }
  .contact-list li {
    display: flex;
    align-items: center;
    gap: 8px;
    font-family: "Arimo", sans-serif;
    font-size: 15px;
    line-height: 1.55;
    color: var(--ink-soft);
  }
  .contact-list svg { width: 12px; height: 12px; flex: none; }

  .brand-ghost {
    position: absolute;
    right: 28px;
    bottom: 14px;
    font-family: "Jost", sans-serif;
    font-weight: 400;
    font-size: 38px;
    line-height: 1;
    letter-spacing: 0.06em;
    text-transform: uppercase;
    color: var(--ghost);
  }
</style>
</head>
<body>
<main class="canvas">
  <section class="card card--front" aria-label="Card front">
    <p class="company-name">Bellhaven Group of Companies</p>

    <div class="person">
      <h1 class="person__name">Tobias Quenby</h1>
      <p class="person__title">Chief Executive Officer</p>
      <div class="person__rule"></div>
      <ul class="contact-list">
        <li>
          <svg viewBox="0 0 12 12" aria-hidden="true"><path d="M2.6 1 L4.4 1 L5 3.6 L3.9 4.5 Q5 6.9 7.5 8.1 L8.4 7 L11 7.6 L11 9.4 Q10.8 11 9.2 11 Q1 10.4 1 2.6 Q1 1 2.6 1 Z" fill="var(--ink)"/></svg>
          780-555-0187
        </li>
        <li>
          <svg viewBox="0 0 12 12" aria-hidden="true"><rect x="0.5" y="2" width="11" height="8" fill="var(--ink)"/><path d="M0.8 2.4 L6 6.6 L11.2 2.4" stroke="var(--paper)" stroke-width="1" fill="none"/></svg>
          tobiasquenby@bellhavengroup.example
        </li>
        <li>
          <svg viewBox="0 0 12 12" aria-hidden="true"><circle cx="6" cy="6" r="5.2" fill="var(--ink)"/><path d="M1 6 H11 M6 1 Q3 6 6 11 M6 1 Q9 6 6 11" stroke="var(--paper)" stroke-width="0.8" fill="none"/></svg>
          www.bellhavengroup.example
        </li>
      </ul>
    </div>

    <p class="brand-ghost" aria-hidden="true">Bellhaven</p>
  </section>

  <section class="card card--back" aria-label="Card back">
    <p class="company-name">Bellhaven Group of Companies</p>
  </section>
</main>
</body>
</html>
```